Local fast-growing company in the service sector

We are looking for a modern business card design, which should also appear on our letterheads

Target Market(s)

Private and industrial sectors

Contact Information for Business Card

Vorname Name
Kellberger Str. 18
71409 Lindenau
Tel.: 07146-839214-0
Name@agentur-kvtl.de

Colors
9d9d9d
919191
aaaaaa

Requirements
Must have
• The logo (file) in silver

```html
<!DOCTYPE html>
<html lang="de">
<head>
<meta charset="utf-8">
<title>KVTL Visitenkarte</title>
<link href="https://fonts.googleapis.com/css2?family=Roboto:wght@400;500;700&family=Roboto+Condensed:wght@500&display=swap" rel="stylesheet">
<style>
  :root {
    --backdrop: #d2a47b;
    --card-dark: #1b1c1e;
    --card-light: #f4f4f4;
    --silver: #aaaaaa;
    --silver-mid: #9d9d9d;
    --silver-light: #c9c9c9;
    --text-grey: #555555;
    --name-grey: #858585;
    --rule: #919191;
    --icon-grey: #6a6a6a;
  }
  * { margin: 0; padding: 0; box-sizing: border-box; }
  html, body { width: 1200px; height: 960px; overflow: hidden; }
  body {
    background: var(--backdrop);
    font-family: "Roboto", Arial, sans-serif;
    position: relative;
  }
  .card {
    position: absolute;
    left: 320px;
    width: 600px;
    border-radius: 18px;
  }
  .card--front {
    top: 100px;
    height: 340px;
    background: var(--card-dark);
  }
  .card--back {
    top: 493px;
    height: 330px;
    background: var(--card-light);
  }
  .front-brand {
    position: absolute;
    top: 100px;
    left: 0;
    width: 100%;
    display: flex;
    justify-content: center;
    align-items: center;
    gap: 22px;
  }
  .brand-square {
    width: 54px;
    height: 54px;
    background: var(--silver-light);
  }
  .front-brand .brand-name {
    font-weight: 700;
    font-size: 96px;
    line-height: 1;
    color: var(--silver-light);
    letter-spacing: 2px;
  }
  .front-url {
    position: absolute;
    top: 292px;
    width: 100%;
    text-align: center;
    color: #ffffff;
    font-size: 15px;
    letter-spacing: 6.5px;
  }
  .back-brand {
    position: absolute;
    top: 68px;
    right: 32px;
    display: flex;
    align-items: center;
    gap: 16px;
  }
  .back-brand .brand-square {
    width: 40px;
    height: 40px;
    background: var(--silver);
  }
  .back-brand .brand-name {
    font-weight: 700;
    font-size: 64px;
    line-height: 1;
    color: var(--silver);
    letter-spacing: 1px;
  }
  .person-name {
    position: absolute;
    left: 30px;
    top: 220px;
    font-family: "Roboto Condensed", "Arial Narrow", sans-serif;
    font-weight: 500;
    font-size: 24px;
    color: var(--name-grey);
  }
  .rule {
    position: absolute;
    left: 30px;
    right: 33px;
    top: 254px;
    height: 1px;
    background: var(--rule);
  }
  .contact-list {
    position: absolute;
    left: 30px;
    top: 264px;
    list-style: none;
    font-size: 14px;
    color: var(--text-grey);
    line-height: 20px;
  }
  .contact-list li { display: flex; align-items: center; gap: 8px; }
  .contact-list svg { width: 13px; height: 13px; fill: var(--icon-grey); }
  .address {
    position: absolute;
    right: 33px;
    top: 264px;
    font-style: normal;
    text-align: right;
    font-size: 14px;
    line-height: 20px;
    color: var(--text-grey);
  }
</style>
</head>
<body>
  <section class="card card--front">
    <div class="front-brand">
      <span class="brand-square"></span>
      <span class="brand-name">KVTL</span>
    </div>
    <p class="front-url">www.agentur-kvtl.de</p>
  </section>

  <section class="card card--back">
    <div class="back-brand">
      <span class="brand-square"></span>
      <span class="brand-name">KVTL</span>
    </div>
    <h1 class="person-name">LENA HARTMANN</h1>
    <div class="rule"></div>
    <ul class="contact-list">
      <li>
        <svg viewBox="0 0 24 24" aria-hidden="true"><path d="M6.6 10.8a15.1 15.1 0 0 0 6.6 6.6l2.2-2.2a1 1 0 0 1 1-.25 11.4 11.4 0 0 0 3.6.57 1 1 0 0 1 1 1V20a1 1 0 0 1-1 1A17 17 0 0 1 3 4a1 1 0 0 1 1-1h3.5a1 1 0 0 1 1 1c0 1.25.2 2.45.57 3.57a1 1 0 0 1-.25 1z"/></svg>
        07146-839214-0
      </li>
      <li>
        <svg viewBox="0 0 24 24" aria-hidden="true"><path d="M2 5h20v14H2z"/><path d="M3 6l9 7 9-7" fill="none" stroke="#f4f4f4" stroke-width="1.6"/></svg>
        Name@agentur-kvtl.de
      </li>
    </ul>
    <address class="address">
      Kellberger Str. 18<br>
      71409 Lindenau
    </address>
  </section>
</body>
</html>
```